Coaching landingpage/salespage need a layout

Hi!
We are two people from Sweden looking for help to design our coaching landingpage/salespage.

What about:
We need a nice modern timeless appealing Photoshop layout (landingpage) for our coaching page where we coach people to “how to get a richer lifestyle”.

Style of page:
We want the site to reflect seriousness but still harmonic. We would like somewhat colorful and (but not too crazy). After all, we are coaching about investments and private economy.
Responsive layout – consider stacking order when scaling down window width. Fullpage-design where content areas are 960 grid/max-width.

----------------------------------------------------------------------------
Content on page:
*Headersection – Logo and header image with the two coaches together and space for later on adding a video.

*On the landingpage the customers can read up on what we mean by a richer lifestyle (use dummy text). We show our Vardagskompassen (= Lifestyle matrix) and a little description about that. If the customers want to know more, they can click "read more (or a symbolic icon that relates to read more)" to expand a hidden div (section) where they can read more about Vardagskompassen. They can also minimize the section.

*3-4 Unique selling points “Four reasons why choose coaching” with nice designed number-icons and some place for text.

*The customer should also be able to read something about what happens during a typical coaching session, some bullets that summarize it (use dummy text) and a couple of headlines, maybe 3 or 4 (about what they need to prepare for themselves .eg Skype, headset/microphone etc).

*Offer/product section: A section where the customer can see what services we provide, choose product and click order. When customer click order they will arrive to an order-page (this one you don’t have to design) .
Our products are as followed: Bronze (single coaching session), Silver (small-package), Gold (large-package). Use provided graphics for these products.

*Testimonials section. Currently we have 2 good testimonials, but only with text no portrait picture.

Testimonial1: “Uppiggande och inspirerande! Kommer med enkla vardagstips såväl som svårare tips. Ett roligt sätt att få en spark i baken, så att ekonomi-energin bibehålls! Tack för ett bra samtal!" - Helena Brattvik

Testimonial2: "Värdefullast för mig var kunskapen om alternativa investeringssställen som inte är börs eller eget ägande." - Annika Sjöstedt

*Section with portraits and info about the coaches (currently 2 coaches, but in future will be several, so a design-section that’s lets us add more coaches).

*Footer-section
------------------------------------------------------------------------

Colors:
Use Vardagskompassen (attached file) as colorinspiration. Doesn’t have to be exactly those colors, you can use similar colors if it is more pleasing to the eye and you can also use complementary colors.

Currently we have tried of our own but don't really nail it with any apealing design. This is what we have done so far but we want to replace it with your more professional design:

https://www.harborkite.se/full/Page/coaching13
-------------------------------------------------------------

SUMMARIZE of the above design-description:

* Our logo (attached psd-file with smart-object. You can try different colors with color-overlay)

*Apealing headerimage with portrait (attached file "big_portrait")

*Introduction text (use dummy text about 100 words)

*Text about Vardagskompassen (use dummy text about 200 words)

*Vardagskompassen (attached psd-file with smart-object)

*What we are covering during a coaching session (dummy text about 200 words and about 5 or 6 bullets)

*3-4 Unique Selling Points with stylish number icons (not 2 small) and some text.
*Our offers Bronze, Silver, Gold (attached pictures)
*Testimonials
*Picture & info about coaches (attached pictures, choose whichever suits you)
*Footer

Please comment if there are questions.

Target Market(s)

People who want to learn how to create a richer lifestyle which involves more freedom and a better well-being

Number of Pages Required

1 page

Font styles to use
Sans Serif
Other font styles liked:
• Roboto

Requirements
Should not have
• A cheezy unmodern landingpage with lots of texts and 10 sign-up buttons.
• This page is not a site about capturing emails and building lists by provide a "best-guide-for-something". It´s about getting people to book and pay for one or more coaching-sessions.

```html
<!DOCTYPE html>
<html lang="sv">
<head>
<meta charset="utf-8">
<title>Harbor Kite – Coaching</title>
<link rel="stylesheet" href="https://fonts.googleapis.com/css2?family=Source+Sans+3:wght@300;400;600;700&display=swap">
<style>
:root{
  --navy:#16254f;
  --navy-deep:#0d1736;
  --brand:#2c4a8c;
  --brand-btn:#5a76a8;
  --ink:#333a45;
  --pale-blue:#d8e1f0;
  --charcoal:#1c202c;
  --light-grey:#ebebeb;
  --white:#ffffff;
  --line:#d5d9e0;
}
*{margin:0;padding:0;box-sizing:border-box}
html,body{width:1200px;height:4255px;overflow:hidden}
body{font-family:"Source Sans 3",Arial,sans-serif;color:var(--ink);background:var(--white);position:relative}
.section{position:absolute;left:0;width:1200px}
.section-title{position:absolute;left:0;width:1200px;text-align:center;font-size:30px;font-weight:400;letter-spacing:.5px;color:var(--brand)}
.section-title.light{color:var(--white)}

/* header */
.hero{top:0;height:510px;background:linear-gradient(180deg,#1a2b5c 0%,#14224d 55%,#0e1838 100%)}
.hero-bg{position:absolute;inset:0}
.logo{position:absolute;left:175px;top:40px;display:flex;align-items:center;gap:10px;color:var(--white);font-size:25px;font-weight:600;letter-spacing:1px;text-transform:uppercase}
.logo-square{width:14px;height:14px;background:var(--white)}
.main-nav{position:absolute;left:453px;top:46px;display:flex;gap:26px}
.main-nav a{color:var(--white);text-decoration:none;font-size:13px;font-weight:600;text-transform:uppercase;letter-spacing:.3px}
.video-frame{position:absolute;left:182px;top:176px;width:436px;height:221px;background:#eef0f5;padding:10px;box-shadow:0 4px 14px rgba(0,0,0,.4)}
.video-area{width:100%;height:100%;background:linear-gradient(135deg,#9ca2ab,#d7dade 55%,#7f858e)}
.play{position:absolute;left:50%;top:50%;transform:translate(-50%,-50%)}
.coach-photo{position:absolute;left:596px;top:213px;width:510px;height:297px;background:linear-gradient(180deg,#3a3f4a 0%,#23262e 60%,#15171c 100%)}
.name-tag{position:absolute;color:var(--white);font-weight:700;font-size:17px;line-height:17px;text-transform:uppercase}
.name-tag small{display:block;font-weight:400;font-size:10px;text-transform:none;margin-top:3px}
.arrow{position:absolute;top:243px}

/* about */
.about{top:510px;height:548px;background:var(--white)}
.matrix{position:absolute;left:241px;top:157px;width:213px;height:241px;background:linear-gradient(135deg,#d7dfe8 0%,#c9d3de 100%)}
.about-text{position:absolute;left:511px;top:178px;width:595px;font-size:13.5px;line-height:22px;color:var(--ink)}
.about-text p+p{margin-top:14px}
.read-more{position:absolute;left:0;width:1200px;top:432px;text-align:center;font-size:13px;text-transform:uppercase;color:var(--ink)}
.read-more svg{display:block;margin:0 auto 6px}

/* reasons */
.reasons{top:1058px;height:692px;background:linear-gradient(160deg,#3d4a6b 0%,#2b3655 45%,#1c2642 100%)}
.reasons-bg{position:absolute;inset:0;background:radial-gradient(ellipse at 75% 40%,rgba(150,120,110,.35),transparent 55%)}
.divider{position:absolute;left:601px;top:192px;width:1px;height:480px;background:rgba(255,255,255,.45)}
.reason{position:absolute;width:380px;color:var(--white)}
.reason-num{position:absolute;left:0;top:0;font-size:104px;font-weight:300;line-height:100px}
.reason-title{position:absolute;left:107px;top:10px;display:flex;align-items:center;gap:12px;font-size:29px;font-weight:400}
.reason-text{position:absolute;left:107px;top:64px;width:270px;font-size:11.5px;line-height:18px;opacity:.9}

/* session */
.session{top:1750px;height:590px;background:var(--pale-blue)}
.session-col{position:absolute;top:200px;width:262px}
.session-col h3{font-size:19px;line-height:23px;font-weight:600;color:var(--brand)}
.session-col ul{list-style:none;margin-top:36px}
.session-col li{position:relative;padding-left:30px;font-size:11px;line-height:16px;color:var(--ink);margin-bottom:25px}
.session-col li::before{content:"›";position:absolute;left:4px;top:-3px;font-size:17px;color:var(--ink)}

/* offers */
.offers{top:2340px;height:680px;background:var(--white)}
.offers-intro{position:absolute;left:210px;width:780px;top:160px;text-align:center;font-size:14px;line-height:21px;color:var(--ink)}
.offer-card{position:absolute;top:321px;width:273px;height:275px;border:1px solid var(--line);text-align:center}
.medal{position:absolute;left:50%;top:-79px;width:170px;height:170px;margin-left:-85px}
.medal.bronze{background:#c47640}
.medal.silver{background:#bdbdbd}
.medal.gold{background:#e2ad2c}
.offer-name{position:absolute;left:0;width:100%;top:120px;font-size:26px;color:var(--brand)}
.offer-sub{position:absolute;left:0;width:100%;top:155px;font-size:13px;color:var(--brand)}
.offer-price{position:absolute;left:0;width:100%;top:178px;font-size:27px;font-weight:700;color:var(--brand)}
.order-btn{position:absolute;left:50%;margin-left:-68px;top:224px;width:136px;height:43px;line-height:43px;background:var(--brand-btn);color:var(--white);font-size:13px;font-weight:700;text-transform:uppercase;text-decoration:none}

/* testimonials */
.testimonials{top:3020px;height:440px;background:var(--charcoal)}
.quote-photo{position:absolute;width:85px;height:77px;border:3px solid var(--white);background:linear-gradient(160deg,#8fa38a,#5c6f58)}
.quote-text{position:absolute;width:290px;font-size:13px;line-height:20px;color:#d8dbe2}
.quote-name{position:absolute;font-size:19px;color:var(--white)}

/* coaches */
.coaches{top:3460px;height:583px;background:var(--light-grey)}
.portrait{position:absolute;top:214px;width:159px;height:159px;border-radius:50%;border:6px solid var(--brand);background:linear-gradient(160deg,#9aa9b8,#55606c)}
.coach-name{position:absolute;top:262px;font-size:26px;line-height:25px;font-weight:600;color:var(--brand);text-transform:uppercase}
.coach-mail{position:absolute;top:318px;font-size:17px;color:var(--brand)}
.coach-bio{position:absolute;top:388px;width:380px;font-size:13px;line-height:21px;color:var(--ink)}

/* footer */
.site-footer{top:4043px;height:212px;background:var(--white);text-align:center}
.footer-logo{position:absolute;left:0;width:1200px;top:56px;display:flex;justify-content:center;align-items:center;gap:10px;font-size:24px;font-weight:600;letter-spacing:1px;text-transform:uppercase;color:var(--navy)}
.footer-logo .logo-square{background:var(--navy)}
.footer-nav{position:absolute;left:0;width:1200px;top:120px;display:flex;justify-content:center;gap:26px}
.footer-nav a{font-size:12px;text-transform:uppercase;color:var(--ink);text-decoration:none}
.copyright{position:absolute;left:0;width:1200px;top:150px;font-size:11px;text-transform:uppercase;color:var(--ink)}
</style>
</head>
<body>

<header class="section hero">
  <div class="hero-bg" role="img" aria-label="Header photo: dark blue evening sky over a landscape"></div>
  <div class="logo"><span class="logo-square"></span>Harbor Kite</div>
  <nav class="main-nav">
    <a href="#">Home</a><a href="#">About us</a><a href="#">Why choose coaching</a><a href="#">Offers/product</a><a href="#">Testimonials</a><a href="#">Contact us</a>
  </nav>
  <svg class="arrow" style="left:68px" width="20" height="24" viewBox="0 0 20 24"><path d="M14 3 5 12l9 9" fill="none" stroke="#fff" stroke-width="3"/></svg>
  <svg class="arrow" style="left:1113px" width="20" height="24" viewBox="0 0 20 24"><path d="m6 3 9 9-9 9" fill="none" stroke="#fff" stroke-width="3"/></svg>
  <div class="video-frame">
    <div class="video-area" role="img" aria-label="Video still: a couple celebrating outdoors"></div>
    <svg class="play" width="76" height="76" viewBox="0 0 76 76"><circle cx="38" cy="38" r="35" fill="rgba(0,0,0,.55)" stroke="#fff" stroke-width="3"/><path d="M30 24v28l22-14z" fill="#fff"/></svg>
  </div>
  <div class="coach-photo" role="img" aria-label="Portrait photo of the two coaches side by side"></div>
  <div class="name-tag" style="left:800px;top:326px">Joakim<br>Lindqvist<small>joakim@harborkite.se</small></div>
  <div class="name-tag" style="left:940px;top:284px;width:160px;text-align:right">Niklas<br>Berglund<small>niklas@harborkite.se</small></div>
</header>

<section class="section about">
  <h2 class="section-title" style="top:92px">ABOUT VARDAGSKOMPASSEN</h2>
  <div class="matrix" role="img" aria-label="Vardagskompassen illustration: the lifestyle matrix with four coloured fields"></div>
  <div class="about-text">
    <p>Sed ut perspiciatis unde omnis iste natus error sit voluptatem accusantium doloremque laudantium, totam rem aperiam, eaque ipsa quae ab illo inventore veritatis et quasi architecto beatae vitae dicta sunt explicabo. Nemo enim ipsam voluptatem quia voluptas sit aspernatur aut odit aut fugit, sed quia consequuntur magni dolores eos qui ratione voluptatem sequi nesciunt.</p>
    <p>Neque porro quisquam est, qui dolorem ipsum quia dolor sit amet, consectetur, adipisci velit, sed quia non numquam eius modi tempora incidunt ut labore et dolore magnam aliquam quaerat voluptatem.</p>
  </div>
  <div class="read-more">
    <svg width="36" height="36" viewBox="0 0 36 36"><circle cx="18" cy="18" r="16" fill="none" stroke="#333a45" stroke-width="2"/><path d="M10 18h15M19 12l6 6-6 6" fill="none" stroke="#333a45" stroke-width="2"/></svg>
    Read more
  </div>
</section>

<section class="section reasons">
  <div class="reasons-bg" role="img" aria-label="Background photo: a smiling couple in soft evening light"></div>
  <h2 class="section-title light" style="top:132px">FOUR REASONS WHY CHOOSE COACHING</h2>
  <div class="divider"></div>
  <div class="reason" style="left:213px;top:212px">
    <div class="reason-num">1</div>
    <div class="reason-title"><svg width="24" height="24" viewBox="0 0 24 24"><path d="M4 20 14 10M11 5l8 8-3 3-8-8z" stroke="#5b8fe0" stroke-width="3" fill="#5b8fe0"/></svg>Åtagande</div>
    <p class="reason-text">Alla kan sätta mål, men långt ifrån alla har en förmåga att fullfölja dem. Som coach kommer vi vara motivatorn som puttar dig och ser till att målen som vi kommer överens om, når fram på vägen mot dem.</p>
  </div>
  <div class="reason" style="left:653px;top:212px">
    <div class="reason-num">2</div>
    <div class="reason-title"><svg width="24" height="24" viewBox="0 0 24 24"><path d="M4 3v19" stroke="#5b8fe0" stroke-width="2.5"/><path d="M5 4h15l-4 5 4 5H5z" fill="#5b8fe0"/></svg>Utmanande</div>
    <p class="reason-text">Alla kan sätta mål, men långt ifrån alla har en förmåga att fullfölja dem. Som coach kommer vi vara motivatorn som puttar dig och ser till att målen som vi kommer överens om, når fram på vägen mot dem.</p>
  </div>
  <div class="reason" style="left:213px;top:418px">
    <div class="reason-num">3</div>
    <div class="reason-title"><svg width="24" height="24" viewBox="0 0 24 24"><circle cx="12" cy="12" r="9" fill="none" stroke="#5b8fe0" stroke-width="3"/><circle cx="12" cy="12" r="4" fill="none" stroke="#5b8fe0" stroke-width="2"/><path d="M5 5l4 4M19 5l-4 4M5 19l4-4M19 19l-4-4" stroke="#5b8fe0" stroke-width="2"/></svg>Stöd</div>
    <p class="reason-text">Alla kan sätta mål, men långt ifrån alla har en förmåga att fullfölja dem. Som coach kommer vi vara motivatorn som puttar dig och ser till att målen som vi kommer överens om, når fram på vägen mot dem.</p>
  </div>
  <div class="reason" style="left:653px;top:418px">
    <div class="reason-num">4</div>
    <div class="reason-title"><svg width="24" height="24" viewBox="0 0 24 24"><rect x="2" y="7" width="20" height="14" rx="2" fill="#5b8fe0"/><path d="M8 7V4h8v3" fill="none" stroke="#5b8fe0" stroke-width="2"/></svg>Du är unik</div>
    <p class="reason-text">Alla kan sätta mål, men långt ifrån alla har en förmåga att fullfölja dem. Som coach kommer vi vara motivatorn som puttar dig och ser till att målen som vi kommer överens om, når fram på vägen mot dem.</p>
  </div>
</section>

<section class="section session">
  <h2 class="section-title" style="top:110px;color:var(--navy-deep)">WHAT HAPPENS DURING A TYPICAL COACHING SESSION</h2>
  <div class="session-col" style="left:176px">
    <h3>Sed ut perspiciatis unde omnis iste natus error sit voluptatem accusantium doloremque</h3>
    <ul>
      <li>At vero eos et accusamus et iusto odio dignissimos ducimus qui blanditiis praesentium</li>
      <li>Molestias excepturi sint occaecati cupiditate non num facilis est et expedita distinctio.</li>
      <li>Nam libero tempore, cum soluta nobis est</li>
      <li>Eligendi optio cumque nihil impedit quo minus id quod maxime placeat facere possimus.</li>
    </ul>
  </div>
  <div class="session-col" style="left:465px">
    <h3>Unde omnis iste natus error sit voluptatem accusantium doloremque laudantium</h3>
    <ul>
      <li>At vero eos et accusamus et iusto odio dignissimos ducimus qui blanditiis praesentium</li>
      <li>Molestias excepturi sint occaecati cupiditate non num facilis est et expedita distinctio.</li>
      <li>Nam libero tempore, cum soluta nobis est</li>
      <li>Eligendi optio cumque nihil impedit quo minus id quod maxime placeat facere possimus.</li>
    </ul>
  </div>
  <div class="session-col" style="left:755px">
    <h3>Perspiciatis unde omnis iste natus error sit voluptatem accusantium dolorem</h3>
    <ul>
      <li>At vero eos et accusamus et iusto odio dignissimos ducimus qui blanditiis praesentium</li>
      <li>Molestias excepturi sint occaecati cupiditate non num facilis est et expedita distinctio.</li>
      <li>Nam libero tempore, cum soluta nobis est</li>
      <li>Eligendi optio cumque nihil impedit quo minus id quod maxime placeat facere possimus.</li>
    </ul>
  </div>
</section>

<section class="section offers">
  <h2 class="section-title" style="top:104px">OFFERS/ PRODUCTS</h2>
  <p class="offers-intro">Vill du ha något du tidigare inte haft? Börja då utforma en livsstil du tidigare inte levt. Vi på Harbor Kite hjälper dig med detta genom livsstilscoaching. Nedan kan du välja något av våra coachingpaket.</p>
  <div class="offer-card" style="left:176px">
    <div class="medal bronze" role="img" aria-label="Bronze package graphic"></div>
    <div class="offer-name">Engångsession</div>
    <div class="offer-sub">Inkluderar 1 session</div>
    <div class="offer-price">650 SEK</div>
    <a class="order-btn" href="#">Order now</a>
  </div>
  <div class="offer-card" style="left:465px">
    <div class="medal silver" role="img" aria-label="Silver package graphic"></div>
    <div class="offer-name">Engångsession</div>
    <div class="offer-sub">Inkluderar 1 session</div>
    <div class="offer-price">3050 SEK</div>
    <a class="order-btn" href="#">Order now</a>
  </div>
  <div class="offer-card" style="left:755px">
    <div class="medal gold" role="img" aria-label="Gold package graphic"></div>
    <div class="offer-name">Engångsession</div>
    <div class="offer-sub">Inkluderar 1 session</div>
    <div class="offer-price">5800 SEK</div>
    <a class="order-btn" href="#">Order now</a>
  </div>
</section>

<section class="section testimonials">
  <h2 class="section-title light" style="top:128px">TESTIMONIALS</h2>
  <div class="quote-photo" style="left:176px;top:223px" role="img" aria-label="Portrait photo of Helena Brattvik"></div>
  <p class="quote-text" style="left:298px;top:218px">"Uppiggande och inspirerande! Kommer med enkla vardagstips såväl som svårare tips. Ett roligt sätt att få en spark i baken, så att ekonomi-energin bibehålls! Tack för ett bra samtal!"</p>
  <div class="quote-name" style="left:298px;top:334px">Helena Brattvik</div>
  <div class="quote-photo" style="left:628px;top:223px" role="img" aria-label="Portrait photo of Annika Sjöstedt"></div>
  <p class="quote-text" style="left:732px;top:218px">"Värdefullast för mig var kunskapen om alternativa investeringssställen som inte är börs eller eget ägande."</p>
  <div class="quote-name" style="left:732px;top:334px">Annika Sjöstedt</div>
</section>

<section class="section coaches">
  <h2 class="section-title" style="top:112px">ABOUT COACHES</h2>
  <div class="portrait" style="left:176px" role="img" aria-label="Portrait photo of Joakim Lindqvist"></div>
  <div class="coach-name" style="left:360px">Joakim<br>Lindqvist</div>
  <div class="coach-mail" style="left:360px">joakim@harborkite.se</div>
  <p class="coach-bio" style="left:176px">Mångsidig investerare med fokus på alternativa och fastighetsinvesteringar. Förutom börsen investerar Joakim i onoterade startup-bolag och olika internetbaserade investeringar såsom P2P-lending, onlinespel och appar.</p>
  <div class="portrait" style="left:647px" role="img" aria-label="Portrait photo of Niklas Berglund"></div>
  <div class="coach-name" style="left:826px">Niklas<br>Berglund</div>
  <div class="coach-mail" style="left:826px">niklas@harborkite.se</div>
  <p class="coach-bio" style="left:612px">Niklas har en bred bakgrund inom ekonomi och IT. Som investerare ligger hans fokus på utdelningsaktier, fastigheter och internetbaserat entreprenörskap. Han har också en lång erfarenhet och en stor passion av att hjälpa människor och verksamheter att utvecklas på olika sätt, i grunden har detta alltid handlat.</p>
</section>

<footer class="section site-footer">
  <div class="footer-logo"><span class="logo-square"></span>Harbor Kite</div>
  <nav class="footer-nav">
    <a href="#">Home</a><a href="#">About us</a><a href="#">Why choose coaching</a><a href="#">Offers/product</a><a href="#">Testimonials</a><a href="#">Contact us</a>
  </nav>
  <p class="copyright">© 2016 Company Name | All rights reserved</p>
</footer>

</body>
</html>
```